Hartwell Estates Business Cards

I would like a business card that includes myself and my partner.
Includes: Logo, office #, email, website, our names, our numbers and possibly the address. I would also like the logo to be embossed and the card to be horizontal.
There is a photo of our yard signs to give you an idea of the colors of our business.

Target Market(s)

Everyone in real estate market.
We are in a rural area. Our clientele are from all socioeconomic backgrounds.

Industry/Entity Type

Real Estate Agent

Contact Information for Business Card

Company Name: Hartwell Estates
Our Names, Titles & Cell #'s : Dana Pembrook-Broker (555).317.6624, Marla Pembrook-Realtor (555).609.1385
Office #: (555).240.3918
Website: hartwellestates-demo.com
Joint Email: pembrook@hartwellestates-demo.com
Office Address: 418B W. Calloway Ave.
Dunmere, KS. 70913

Font styles to use
Serif

Requirements
Must have
• HORIZONTAL, Logo, Myself and my partners names, Our cell #'s, our office #, our website, our email address
Nice to have
• Embossed logo, office address, our titles.

```html
<!DOCTYPE html>
<html lang="en">
<head>
<meta charset="utf-8">
<title>Hartwell Estates Business Cards</title>
<link rel="stylesheet" href="https://fonts.googleapis.com/css2?family=Source+Sans+3:wght@400;600&display=swap">
<style>
  :root {
    --plum: #4a2468;
    --white: #ffffff;
    --backdrop: #ece9ef;
    --soft-white: rgba(255,255,255,0.92);
  }
  * { box-sizing: border-box; margin: 0; padding: 0; }
  html, body {
    width: 1200px; height: 900px; overflow: hidden;
    background: var(--backdrop);
    font-family: "Source Sans 3", "Myriad Pro", Arial, sans-serif;
  }
  .canvas {
    width: 1200px; height: 900px;
    display: flex; flex-direction: column;
    align-items: center; justify-content: center; gap: 44px;
  }
  .card {
    position: relative;
    width: 640px; height: 366px;
    overflow: hidden;
    box-shadow: 0 6px 18px rgba(40, 20, 60, 0.18);
  }

  /* Front */
  .card--front { background: var(--plum); color: var(--white); }
  .brand {
    display: flex; align-items: center; gap: 14px;
    font-weight: 600; letter-spacing: 0.5px; white-space: nowrap;
  }
  .brand__dot {
    width: 26px; height: 26px; border-radius: 50%;
    background: currentColor; flex: none;
  }
  .card--front .brand {
    position: absolute; left: 50%; top: 118px; transform: translateX(-50%);
    font-size: 46px;
  }
  .card--front .website {
    position: absolute; left: 0; right: 0; top: 222px;
    text-align: center; font-size: 15px; letter-spacing: 0.3px;
  }

  /* Back */
  .card--back { background: var(--plum); color: var(--white); }
  .card__band {
    position: absolute; left: 0; top: 0; width: 100%; height: 150px;
    background: var(--white);
  }
  .card--back .brand {
    position: absolute; left: 50%; top: 50px; transform: translateX(-50%);
    font-size: 42px; color: var(--plum);
  }
  .contact {
    position: absolute; font-size: 17px; line-height: 1.3;
  }
  .contact__name { font-weight: 600; font-size: 20px; }
  .contact--broker { left: 40px; top: 184px; }
  .contact--realtor { right: 40px; top: 184px; text-align: right; }
  .contact__office { margin-top: 18px; }
  .contact__line { display: flex; align-items: center; gap: 10px; font-size: 17px; }
  .contact__line svg { width: 15px; height: 15px; flex: none; }
  .address { margin-top: 22px; color: var(--soft-white); font-size: 16px; }
</style>
</head>
<body>
<main class="canvas">

  <section class="card card--front" aria-label="Business card front">
    <div class="brand"><span class="brand__dot"></span>Hartwell Estates</div>
    <p class="website">www.hartwellestates-demo.com</p>
  </section>

  <section class="card card--back" aria-label="Business card back">
    <div class="card__band"></div>
    <div class="brand"><span class="brand__dot"></span>Hartwell Estates</div>

    <div class="contact contact--broker">
      <p class="contact__name">Dana Pembrook</p>
      <p>Broker</p>
      <p>(555).317.6624</p>
      <div class="contact__office">
        <p class="contact__line">
          <svg viewBox="0 0 16 16" aria-hidden="true"><path fill="#fff" d="M2 6c0-2 2-3 6-3s6 1 6 3v1h-3V5.5H5V7H2zM4 8h8l1.5 5h-11z"/></svg>
          (555).240.3918
        </p>
        <p class="contact__line">
          <svg viewBox="0 0 16 16" aria-hidden="true"><rect x="1" y="3" width="14" height="10" fill="#fff"/><path d="M1.5 3.5L8 9l6.5-5.5" fill="none" stroke="#4a2468" stroke-width="1.3"/></svg>
          pembrook@hartwellestates-demo.com
        </p>
      </div>
    </div>

    <div class="contact contact--realtor">
      <p class="contact__name">Marla Pembrook</p>
      <p>Realtor</p>
      <p>(555).609.1385</p>
      <div class="address">
        <p>418B W. Calloway Ave.</p>
        <p>Dunmere, KS. 70913</p>
      </div>
    </div>
  </section>

</main>
</body>
</html>
```